Trendy eye catching business card for lawn mowing business

Turf Tidy, a local community lawn mowing service, requires an eye catching trendy business card to drop into letterboxes.

We could simply throw something together from a Microsoft Word template, but we are wanting something more than this. Some other business’ images are attached for some inspiration.

We are requiring the card to have Turf Tidy with our slogan, Call The Brindles. In addition, provide details with that we are a local, affordable lawn mowing service, and for other gardening matters to simply just ask!
Plus the relevant contact details, phone, email, social media.

Target Market(s)

Local community members who require assistance with their garden care

Industry/Entity Type

Gardening

Contact Information for Business Card

the name TURF TIDY is our logo
telephone logo 0438 215 967
email logo turftidy@postbox-mail.example
Instagram logo turftidy
Facebook logo turftidy.sth
Lawn Mowing Service
Local Affordable
edge trim, blow and clipping removal included.
Other gardening matters, just ask!

Font styles to use
Serif
Sans Serif
Decorative
Script

Colors
9bcb3c
ffffff

Requirements
Must have
• All the details listed in Business Card Details.
Make these words prominent:
Turf Tidy
Lawn Mowing Service
Local
Affordable
Nice to have
• Our slogan ‘Call The Brindles’ incorporated.
Different colour background for front and reverse side
Greens, white and black colours
Subtle grass blades images incorporated
Should not have
• No images of lawnmowers.
No images of men/cartoons.
No using initials for Turf Tidy

```html
<!DOCTYPE html>
<html lang="en">
<head>
<meta charset="utf-8">
<title>Turf Tidy – Business Card</title>
<link href="https://fonts.googleapis.com/css2?family=Montserrat:wght@500;800;900&family=Poppins:wght@400;500;700&family=Great+Vibes&display=swap" rel="stylesheet">
<style>
  :root{
    --backdrop:#8d8f92;
    --card-light:#e3ede0;
    --forest:#0f5a1c;
    --forest-deep:#0a4a16;
    --leaf:#2f8f22;
    --lime:#4cc11f;
    --lime-bright:#5fd12a;
    --headline:#3a9e25;
    --ink:#1f2a1f;
    --white:#ffffff;
  }
  *{margin:0;padding:0;box-sizing:border-box}
  html,body{width:1200px;height:801px;overflow:hidden}
  body{background:var(--backdrop);position:relative;font-family:"Poppins",sans-serif}

  .card{position:absolute;top:246px;width:540px;height:309px;border-radius:22px;overflow:hidden}

  /* Front */
  .card-front{left:30px;background:var(--card-light)}
  .brand{position:absolute;left:34px;top:0;width:230px;height:100%;display:flex;flex-direction:column;justify-content:center;align-items:center}
  .brand-mark{display:flex;align-items:center;gap:10px}
  .brand-dot{width:18px;height:18px;border-radius:50%;background:var(--leaf)}
  .brand-name{font-family:"Montserrat",sans-serif;font-weight:900;font-size:38px;line-height:1;color:var(--forest);letter-spacing:1px}
  .brand-slogan{font-family:"Great Vibes",cursive;font-size:30px;color:var(--ink);margin-top:8px}
  .divider{position:absolute;left:282px;top:92px;width:1px;height:112px;background:var(--forest)}
  .contact{position:absolute;left:302px;top:84px}
  .person-name{font-family:"Montserrat",sans-serif;font-weight:800;font-size:17px;color:var(--forest);letter-spacing:.5px}
  .person-role{font-weight:500;font-size:14px;color:var(--lime);margin-bottom:10px}
  .contact-list{list-style:none}
  .contact-list li{display:flex;align-items:center;gap:8px;font-size:12.5px;color:var(--ink);line-height:19px}
  .contact-list svg{width:11px;height:11px;flex:none}

  /* Back */
  .card-back{left:630px;background:linear-gradient(180deg,var(--forest-deep) 0%,var(--forest) 45%,var(--leaf) 70%,var(--lime) 100%)}
  .grass{position:absolute;left:0;right:0;bottom:0;height:150px;background:linear-gradient(180deg,rgba(95,209,42,0) 0%,var(--lime) 45%,var(--lime-bright) 100%)}
  .offer{position:absolute;left:0;right:0;top:52px;text-align:center}
  .offer-title{font-family:"Montserrat",sans-serif;font-weight:900;font-size:32px;color:var(--headline);letter-spacing:.5px;line-height:1.05}
  .offer-tag{font-family:"Montserrat",sans-serif;font-weight:800;font-size:26px;color:var(--lime-bright);letter-spacing:1px;margin-top:4px}
  .offer-detail{font-size:14.5px;font-weight:500;color:var(--white);margin-top:12px;line-height:1.3}
  .web{position:absolute;left:0;right:0;bottom:30px;text-align:center;font-family:"Montserrat",sans-serif;font-weight:800;font-size:18px;color:var(--forest-deep);letter-spacing:1.5px}
</style>
</head>
<body>
  <section class="card card-front">
    <div class="brand">
      <div class="brand-mark">
        <span class="brand-dot"></span>
        <span class="brand-name">TURF TIDY</span>
      </div>
      <p class="brand-slogan">Call The Brindles</p>
    </div>
    <div class="divider"></div>
    <div class="contact">
      <p class="person-name">DANIEL BROOKS</p>
      <p class="person-role">President</p>
      <ul class="contact-list">
        <li><svg viewBox="0 0 24 24"><path fill="#1f2a1f" d="M6.6 10.8a15 15 0 0 0 6.6 6.6l2.2-2.2c.3-.3.7-.4 1-.2 1.1.4 2.3.6 3.6.6.6 0 1 .4 1 1V20c0 .6-.4 1-1 1A17 17 0 0 1 3 4c0-.6.4-1 1-1h3.5c.6 0 1 .4 1 1 0 1.3.2 2.5.6 3.6.1.3 0 .7-.2 1z"/></svg>0438 215 967</li>
        <li><svg viewBox="0 0 24 24"><rect x="2" y="5" width="20" height="14" rx="2" fill="#1f2a1f"/><path d="M3 6l9 7 9-7" stroke="#e3ede0" stroke-width="2" fill="none"/></svg>turftidy@postbox-mail.example</li>
        <li><svg viewBox="0 0 24 24"><circle cx="12" cy="12" r="9" fill="none" stroke="#1f2a1f" stroke-width="2.5"/></svg>turftidy.example</li>
        <li><svg viewBox="0 0 24 24"><circle cx="12" cy="12" r="9" fill="#1f2a1f"/></svg>turftidy</li>
      </ul>
    </div>
  </section>

  <section class="card card-back">
    <div class="grass" role="img" aria-label="Bright green grass blades rising along the bottom of the card"></div>
    <div class="offer">
      <h1 class="offer-title">LAWN MOWING SERVICE</h1>
      <p class="offer-tag">LOCAL. AFFORDABLE.</p>
      <p class="offer-detail">edge trim, blow &amp; clipping removal included.<br>Other gardening matters, just ask!</p>
    </div>
    <p class="web">WWW.TURFTIDY.EXAMPLE</p>
  </section>
</body>
</html>
```